Revolutionairy Video Marketing Consultant

I will be touring Australia and New Zealand for 6 weeks on a speaking and consulting tour, teaching Real Estate Agents how to show their properties using ClipCast and their iPhones!
Learn more about what we do at www.brightlanestudio.com
I will also hire the project winner to redo the company mainpage and logo.
This will be a two page email flyer. Here's an idea of the flyer text and the artwork I'd like to use:
use the header logo from this page: http://www.keystoneleasinghub.com/
use the photo from my facebook page:
http://www.facebook.com/marcus.ellery7
I can provide other photos of me speaking and consulting too
Here's the basic text:
The World’s Best Property Management Video Expert
In your office for a whole day!
Marcus Ellery from Coral Bay Florida USA (see brightlanestudio.com) will be in Australia and New Zealand in April and May 2012, has only a few spare days in his calendar and is offering you personally his expertise inside individual offices only.
Marcus Ellery can teach you and your team a unique point of difference using simple video technology that will not only give you a unique and hard to beat edge over your competitors with winning new business, but also proven techniques to reduce stress and conflict between you and your tenants and landlords.
Marcus brings his X years of experience to the table and in a complete session you and your team will know:
• How to create an easy, cost effective marketing video tour for your rental properties that will really impress prospective clients with your unique edge, making you the obvious choice over your competitors and easily win your fee!
• Allow prospective tenants to qualify themselves quickly and easily with your property marketing videos, enhancing your letting process.
• How to communicate more effectively with landlords by learning how to use video to show serious repairs and maintenance required and other issues of concern, to allow clients to make quick and informed choices, making your job so much easier!
• Quickly reduce your time and stress with tenant bond disputes by easily adding ingoing and outgoing inspection video footage to your current inspection process, reducing significantly the chance of the tenant wanting to take matters to tribunal.
• Understand the low to no-cost video technology and hosting platforms available to you right now, so you can get started right away!
As a Bonus- contract Marcus for a full day and receive the following further unique and exclusive benefits:
How to get seriously ranked on Searchly!
When most new landlords when online search using Searchly, you cannot afford to come up anywhere else except on the front page. Marcus will also teach you:
• How to get the top ‘A’ pin on the widely used Searchly Maps on page one of Searchly search.
• Know how Marcus got the ‘Search Hat-Trick’ allowing his company to be top listed for his website, marketing videos and maps all at the same time, dominating the front page!
• Another secret to how Marcus overnight tripled his new landlord enquiry rate online, accelerating his rent roll growth.
Full Day- $2500 plus travel expenses (subject to office location)
Half Day- $1650 plus travel expenses (subject to availability and office location)
Don’t Leave it too late- take fast action and book Marcus today!
For enquiries and bookings call Wendy on +61 2 9364-7150 or email wendy@qrta.com.au
Updates
Thanks
Target Market(s)
Owner's of Property Management Businesses in Australia and New Zealand. They like polished looking flyers.
Industry/Entity Type
Marketing
Look and feel
Each slider illustrates characteristics of the customer's brand and the style your logo design should communicate.

```html
<!DOCTYPE html>
<html lang="en">
<head>
<meta charset="utf-8">
<title>Marcus Ellery – Property Management Video Flyer</title>
<link rel="stylesheet" href="https://fonts.googleapis.com/css2?family=Open+Sans:ital,wght@0,400;0,600;0,700;0,800;1,400;1,700;1,800&display=swap">
<style>
  :root{
    --blue:#2c3fd6;
    --blue-deep:#1f2fae;
    --green:#8ee51c;
    --green-box:#c7f08c;
    --lavender:#cdd2f1;
    --red:#ee1c1c;
    --grey-text:#6a6a6a;
    --ink:#1a1a1a;
    --page-edge:#b9bccb;
    --backdrop:#ececec;
  }
  *{box-sizing:border-box;margin:0;padding:0}
  html,body{width:1200px;height:847px;overflow:hidden}
  body{background:var(--backdrop);font-family:"Open Sans",Arial,sans-serif;position:relative}

  .page{position:absolute;top:72px;width:474px;height:669px;background:#fff;border:1px solid var(--page-edge);overflow:hidden}
  .page--left{left:103px}
  .page--right{left:607px}
  .page svg.shape{position:absolute;left:0;top:0}

  /* ---------- left page ---------- */
  .speaker-photo{position:absolute;left:262px;top:13px;width:184px;height:118px;border-radius:14px;background:linear-gradient(135deg,#6b5a48,#c9a27a 55%,#3a3024)}
  .headline{position:absolute;left:13px;top:42px;width:250px;font-style:italic;font-weight:800;color:var(--green);font-size:17px;line-height:21px}
  .subhead{position:absolute;left:13px;top:85px;font-weight:700;color:var(--blue);font-size:16.5px;line-height:22px}
  .intro{position:absolute;left:13px;top:111px;width:455px;font-size:7.3px;line-height:10.2px;color:var(--grey-text)}
  .intro p+p{margin-top:2px}
  .intro b{color:var(--blue)}
  .lead-in{position:absolute;left:13px;top:203px;width:345px;font-style:italic;font-weight:700;color:var(--blue);font-size:8.6px;line-height:11px}

  .topic{position:absolute;width:223px;height:107px;border-radius:9px;padding:7px 6px 0 6px}
  .topic--lav{background:var(--lavender)}
  .topic--green{background:var(--green-box)}
  .topic h3{font-size:8.6px;font-weight:700;color:var(--ink);margin-bottom:3px;white-space:nowrap}
  .topic ul{list-style:none}
  .topic li{font-size:7.4px;line-height:16.5px;color:var(--ink);white-space:nowrap}
  .topic li::before{content:"• "}
  .topic li.wrap{white-space:normal;line-height:16.5px}

  .pricing{position:absolute;left:13px;top:503px;font-weight:700;color:var(--blue);font-size:8.6px;line-height:16px}
  .contact{position:absolute;left:13px;top:587px;color:var(--red);font-size:11px;line-height:19px}
  .contact .phone{font-size:15.5px;font-weight:700}
  .contact b{font-weight:700}

  .sign-art{position:absolute;left:300px;top:460px;width:174px;height:209px;background:linear-gradient(180deg,#f1f1f1 0%,#f1f1f1 30%,#e8403a 30%,#d81818 70%,#ececec 70%)}
  .sign-text{position:absolute;left:320px;top:527px;width:110px;transform:rotate(7deg);color:#fff;font-weight:800;font-size:8.4px;line-height:13px;text-align:center}

  /* ---------- right page ---------- */
  .brand{position:absolute;left:30px;top:28px;display:flex;align-items:center;gap:7px}
  .brand .mark{width:18px;height:18px;background:var(--blue)}
  .brand .name{font-weight:700;color:var(--blue);font-size:14px}
  .portrait{position:absolute;left:293px;top:28px;width:153px;height:168px;border-radius:0 0 0 10px;background:linear-gradient(160deg,#8d6e55,#d8b798 50%,#c9c9c9)}
  .tagline{position:absolute;left:16px;top:170px;font-style:italic;font-weight:800;color:var(--green);font-size:27px;line-height:38px}
  .benefits{position:absolute;left:14px;top:266px;list-style:none}
  .benefits li{font-weight:700;color:var(--green);font-size:16.5px;line-height:34.5px;white-space:nowrap}
  .benefits li::before{content:"• "}
  .promo{position:absolute;right:23px;top:436px;text-align:right;color:#fff;font-weight:700;font-size:15.5px;line-height:23px}
  .promo .gap{display:block;height:12px}
  .quote-photo{position:absolute;left:12px;top:527px;width:98px;height:128px;border:2px solid var(--green);border-radius:8px;background:linear-gradient(170deg,#d4d4d4,#8a8a8a)}
  .quote{position:absolute;left:124px;top:553px;width:330px;font-style:italic;color:var(--blue);font-size:7.4px;line-height:11.2px}
  .quote .mark-q{font-size:20px;font-weight:800;color:var(--green);line-height:0;vertical-align:-6px}
  .quote .open{position:absolute;left:-12px;top:6px}
  .quote cite{display:block;margin-top:3px;font-size:6.8px;color:var(--green);font-style:italic}
</style>
</head>
<body>

<section class="page page--left">
  <svg class="shape" width="474" height="669" viewBox="0 0 474 669" aria-hidden="true">
    <path d="M0,0 H474 V70 Q300,10 0,38 Z" fill="var(--blue)"/>
  </svg>
  <div class="speaker-photo" role="img" aria-label="Photo of Marcus Ellery speaking at a seminar"></div>

  <h1 class="headline">The World’s Best Property Management Video Expert</h1>
  <h2 class="subhead">In your office for a whole day!</h2>
  <div class="intro">
    <p><b>Marcus Ellery</b> from Coral Bay Florida USA<br>(see brightlanestudio.com) will be in Australia and New<br>Zealand in April and May 2012, has only a few spare days in his calendar and is offering you personally his expertise inside individual offices only.</p>
    <p>Marcus Ellery can teach you and your team a unique point of difference using simple video technology that will not only give you a unique and hard to beat edge over your competitors with winning new business, but also proven techniques to reduce stress and conflict between you and your tenants and landlords.</p>
  </div>
  <p class="lead-in">Marcus brings his 30+ years of experience to the table and in a complete session you and your team will know:</p>

  <div class="topic topic--lav" style="left:13px;top:236px">
    <h3>Videos - Real Estate Meets ClipCast</h3>
    <ul>
      <li>document condition at tenant move in and move out</li>
      <li>market your properties online on ClipCast</li>
      <li>easily create 5 new testimonial videos for your websites!</li>
      <li>train your entire staff in a day!</li>
    </ul>
  </div>
  <div class="topic topic--green" style="left:242px;top:236px">
    <h3>Dominate Searchly and Get More Business!</h3>
    <ul>
      <li>be listed first for multiple searches</li>
      <li>get your ‘A’ pin in the Searchly Map</li>
      <li>put your video on page 1 of Searchly!</li>
      <li>dominate Page 1 of Searchly!</li>
    </ul>
  </div>
  <div class="topic topic--green" style="left:13px;top:350px">
    <h3>Go Mobile – Work from Anywhere</h3>
    <ul>
      <li>take your business to the cloud</li>
      <li>get your office on the best email platforms</li>
      <li>wow your clients with a world class phone system</li>
      <li>create your 1,3 &amp; 5 year technology plan</li>
    </ul>
  </div>
  <div class="topic topic--lav" style="left:242px;top:350px">
    <h3>Run Your Rent Roll from Under YOUR Palm Tree</h3>
    <ul>
      <li>stop working IN your office - start working ON it</li>
      <li>create a staff culture that works in your absence</li>
      <li>learn new tools to hire and motivate staff</li>
      <li>implement systems to monitor performance remotely</li>
    </ul>
  </div>

  <div class="pricing">
    Full Day- $2500 plus travel expenses<br>(subject to office location)<br>
    Half Day- $1650 plus travel expenses<br>(subject to availability and office location)
  </div>
  <div class="contact">
    <b>Fo</b>r enquiries and bookings call Wendy on<br>
    <span class="phone">+61 2 9364-7150</span><br>
    or email <b>wendy@qrta.com.au</b>
  </div>

  <div class="sign-art" role="img" aria-label="Illustration of a red real estate sign hanging from a white post"></div>
  <p class="sign-text">Don’t Leave it too late- take fast action and book Marcus today!</p>
</section>

<section class="page page--right">
  <svg class="shape" width="474" height="669" viewBox="0 0 474 669" aria-hidden="true">
    <path d="M0,113 Q240,100 474,112 L474,558 Q250,556 0,440 Z" fill="var(--blue)"/>
  </svg>
  <div class="brand"><span class="mark"></span><span class="name">Keystone Leasing</span></div>
  <div class="portrait" role="img" aria-label="Portrait of Marcus Ellery with signature"></div>

  <h2 class="tagline">Keep Up With Our<br>Rapidly Changing World!</h2>
  <ul class="benefits">
    <li>Train Your Entire Office to Use Videos</li>
    <li>Create Your 'Mobile Management' Strategy</li>
    <li>Run Your Rent Roll from Under a Palm Tree</li>
    <li>Dominate Searchly with Your New 'Search Hat-Trick'</li>
  </ul>
  <p class="promo">Even if you've never made a video before!<br>Real Estate Meets ClipCast<span class="gap"></span>What People Are Saying About<br>Marcus's Training</p>

  <div class="quote-photo" role="img" aria-label="Portrait of Paul Hendry"></div>
  <blockquote class="quote">
    <span class="mark-q open">“</span>
    We are loving videos!<br>
    My team have been really good for integrating video into their day to day work, using them for pre-inspections, post-inspections and marketing videos. Videos like this is unique to our market, and a significant advantage when gaining new clients. We're actually getting new business because we're the only ones offering video! Marcus's methods have helped us grow the business to new heights and if you are a proactive business owner you should be working with him<span class="mark-q">”</span>
    <cite>Paul Hendry, Hendry Real Estate, Ltd</cite>
  </blockquote>
</section>

</body>
</html>
```